HearthMile business card and stationary design

We are looking for a simple yet elegant design for our mortgage company business card and stationary.

The card should include:
Name (Marcus Pell)
Title (CEO)
Phone Number (732-555-0182)
Address (48 Birchwell Court, Suite 314, Ashford Vale, NJ 08412)
Email (email@hearthmile.example)
"NMLS" i.e. (NMLS 61947)
"Company NMLS" (Company NMLS 274615)

Contact Information for Business Card

See above

```html
<!DOCTYPE html>
<html lang="en">
<head>
<meta charset="utf-8">
<title>HearthMile Business Card</title>
<link href="https://fonts.googleapis.com/css2?family=Arimo:wght@400;700&display=swap" rel="stylesheet">
<style>
  :root {
    --navy: #1b2632;
    --blue: #29abe2;
    --ink: #1f2328;
    --paper: #ffffff;
    --stage: #e9eaec;
  }
  * { margin: 0; padding: 0; box-sizing: border-box; }
  html, body { width: 1200px; height: 912px; overflow: hidden; }
  body {
    background: var(--stage);
    font-family: "Arimo", Arial, sans-serif;
    position: relative;
  }
  .card {
    position: absolute;
    width: 540px;
    height: 309px;
    border-radius: 16px;
    overflow: hidden;
    box-shadow: 0 10px 28px rgba(0,0,0,0.18);
  }
  .card-back {
    left: 70px; top: 70px;
    background: var(--navy);
    display: flex; align-items: center; justify-content: center;
  }
  .card-back .wordmark {
    font-size: 62px; font-weight: 700; color: var(--blue); letter-spacing: -0.5px;
  }
  .card-front {
    left: 590px; top: 533px;
    background: var(--paper);
  }
  .card-front .wordmark {
    position: absolute; right: 40px; top: 40px;
    font-size: 40px; font-weight: 700; color: var(--navy); letter-spacing: -0.3px;
    line-height: 1;
  }
  .identity { position: absolute; left: 34px; top: 88px; }
  .identity .name {
    font-size: 21px; font-weight: 700; color: var(--blue); letter-spacing: 0.3px;
    text-transform: uppercase; line-height: 1;
  }
  .identity .title { font-size: 13px; color: var(--ink); margin-top: 6px; line-height: 1; }
  .divider {
    position: absolute; left: 34px; right: 34px; top: 130px;
    height: 1px; background: var(--ink);
  }
  .contact { position: absolute; left: 34px; top: 141px; font-size: 12.5px; color: var(--ink); }
  .contact li { list-style: none; display: flex; align-items: center; gap: 7px; height: 18px; }
  .contact svg { width: 11px; height: 11px; fill: var(--blue); flex: none; }
  .address {
    position: absolute; right: 40px; top: 142px;
    font-size: 12.5px; color: var(--ink); text-align: right; line-height: 1.4;
  }
  .footer-band { position: absolute; left: 0; bottom: 0; width: 540px; height: 80px; }
  .company-nmls {
    position: absolute; right: 28px; bottom: 34px;
    font-size: 12px; color: var(--paper);
  }
</style>
</head>
<body>
  <section class="card card-back" aria-label="Card back">
    <span class="wordmark">HearthMile</span>
  </section>

  <section class="card card-front" aria-label="Card front">
    <span class="wordmark">HearthMile</span>

    <div class="identity">
      <p class="name">Marcus Pell</p>
      <p class="title">CEO</p>
    </div>
    <div class="divider"></div>

    <ul class="contact">
      <li>NMLS 61947</li>
      <li>
        <svg viewBox="0 0 24 24"><path d="M6.6 10.8a15 15 0 0 0 6.6 6.6l2.2-2.2c.3-.3.7-.4 1-.2 1.1.4 2.3.6 3.6.6.6 0 1 .4 1 1V20c0 .6-.4 1-1 1A17 17 0 0 1 3 4c0-.6.4-1 1-1h3.5c.6 0 1 .4 1 1 0 1.3.2 2.5.6 3.6.1.3 0 .7-.2 1z"/></svg>
        732-555-0182
      </li>
      <li>
        <svg viewBox="0 0 24 24"><path d="M2 5h20v14H2z"/><path d="M2 5l10 8 10-8" fill="none" stroke="#fff" stroke-width="2"/></svg>
        email@hearthmile.example
      </li>
      <li>
        <svg viewBox="0 0 24 24"><circle cx="12" cy="12" r="10"/><path d="M2 12h20M12 2c3 3 3 17 0 20M12 2c-3 3-3 17 0 20" fill="none" stroke="#fff" stroke-width="1.5"/></svg>
        www.hearthmile.example
      </li>
    </ul>

    <p class="address">48 Birchwell Court, Suite 314<br>Ashford Vale, NJ 08412</p>

    <svg class="footer-band" viewBox="0 0 540 80" aria-hidden="true">
      <path d="M0 72 L330 40 C345 38 352 30 360 20 C368 10 376 6 392 6 L540 6 L540 80 L0 80 Z" fill="var(--navy)"/>
      <path d="M0 64 L330 32" stroke="var(--blue)" stroke-width="3.5" fill="none"/>
    </svg>
    <span class="company-nmls">Company NMLS 274615</span>
  </section>
</body>
</html>
```